Pull Up Banner - Recruitment Company

We would like a design for a pull up banner.

For context: we are a recruitment business. We specialise in helping people in healthcare industry to find jobs in Australia.

I have come up with several ideas and text for the banner. Feel free to use the following as you see appropriate:

- Our logo (see attached)
- 'Healthcare Recruitment Agency'
- Some sort of imagine / cartoon of medical professionals (ie. doctor, nurse, physiotherapist, speech pathologist). A cartoon is more friendly than committing to a photo
- 'Empowering your next career move'
- 'Discover tailored opportunities based on your career preferences'
- Dot points (allied health, nursing, medical imaging)
- Contact info at the bottom including our website (www.quellastaffing.com.au, our Instagram handle @quellastaffing, Mobile: XXXX XXX XXX. The title section for contact information could be 'Get in touch:'

Feel free to submit a couple of designs and we can merge aspects that look good on your designs and find the perfect fit.
Thank you
Updates

Hello,

Thank you for your initial submissions to this project. I appreciate the time you've invested.

After reviewing the first attempt, I'd like to share some feedback and initial observations:

- Professionalism and engagement: Is the overall appearance of the banner professional? It's crucial that we have a high-quality design as this will represent our business.

- Image selection: The image (whether cartoon or real people) appears quite generic. Please consider submitting the banner with a few different photos in the middle for us to choose from. Ensure the image is a good fit and not simply a generic stock photo.

- Contact section: Kindly remove the phone number; we no longer wish to include it on the banner. Instead, please include our website (www.quellastaffing.com.au) and Instagram handle (@quellastaffing).

- Color scheme: White, black, and red/pink are preferred, or alternatively, blue. However, please avoid incorporating too many different colors as it may detract from the professional appearance.

We will be printing the design on a banner and require it to look professional and engaging.

Thank you once again for your submissions. I hope the feedback provided above is helpful.

Warm regards,

Target Market(s)

Allied Health Australia

Font styles to use
Serif

Colors
0054AA
0677BA
7BADD7
CADEEF
E8F1F8
0094D4
00A9DD
6FCCEA
C7EBF8
E9F6FB
EB3D1F
EC4F4E
F09395
F8D3D4
FCEDEE

```html
<!DOCTYPE html>
<html lang="en">
<head>
<meta charset="utf-8">
<title>Quella Staffing – Pull Up Banner</title>
<link rel="stylesheet" href="https://fonts.googleapis.com/css2?family=Poppins:wght@400;500;600;700;800&display=swap">
<style>
  :root {
    --page-bg: #a9a9a9;
    --banner-bg: #ffffff;
    --ink: #0b0b0b;
    --brand-blue: #2a2fd0;
    --sky-tint: #e9f6fb;
    --sky-mid: #d6eef6;
    --white: #ffffff;
  }
  * { box-sizing: border-box; margin: 0; padding: 0; }
  html, body {
    width: 1200px; height: 4000px; overflow: hidden;
    background: var(--page-bg);
    font-family: "Poppins", sans-serif;
  }
  .banner {
    position: absolute; left: 40px; top: 685px;
    width: 1120px; height: 2630px;
    background: var(--banner-bg);
    box-shadow: 0 20px 40px rgba(0,0,0,.25);
    text-align: center; color: var(--ink);
  }
  .brand-name {
    position: absolute; top: 135px; left: 0; width: 100%;
    font-size: 92px; font-weight: 700; letter-spacing: 6px; line-height: 1;
    color: var(--ink);
  }
  .headline {
    position: absolute; top: 335px; left: 0; width: 100%;
    font-weight: 800; line-height: 1.0; font-size: 114px;
  }
  .headline .accent { color: var(--brand-blue); display: block; }
  .headline .plain { color: var(--ink); display: block; font-size: 122px; }
  .tagline {
    position: absolute; top: 718px; left: 0; width: 100%;
    font-size: 68px; font-weight: 700; line-height: 1.2;
  }
  .illustration {
    position: absolute; top: 890px; left: 0; width: 100%; height: 760px;
    background: linear-gradient(180deg, var(--white) 0%, var(--sky-tint) 25%, var(--sky-mid) 60%, var(--sky-tint) 85%, var(--white) 100%);
  }
  .intro {
    position: absolute; top: 1670px; left: 0; width: 100%;
    font-size: 50px; font-weight: 400; line-height: 1.2;
  }
  .specialties {
    position: absolute; top: 1860px; left: 120px; width: 880px;
    display: flex; justify-content: space-between;
  }
  .specialty { display: flex; flex-direction: column; align-items: center; }
  .specialty svg { width: 100px; height: 110px; }
  .specialty span { margin-top: 18px; font-size: 50px; font-weight: 500; white-space: nowrap; }
  .contact-title {
    position: absolute; top: 2095px; left: 0; width: 100%;
    font-size: 50px; font-weight: 700; letter-spacing: 12px;
  }
  .phone-pill {
    position: absolute; top: 2210px; left: 109px; width: 902px; height: 132px;
    background: var(--brand-blue); border-radius: 66px;
    display: flex; align-items: center; justify-content: center; gap: 24px;
    color: var(--white); font-size: 98px; font-weight: 700;
  }
  .phone-pill svg { width: 84px; height: 84px; }
  .social {
    position: absolute; top: 2360px; left: 0; width: 100%;
    display: flex; justify-content: center; align-items: center; gap: 18px;
    font-size: 48px;
  }
  .social .label { color: var(--brand-blue); font-weight: 400; margin-right: 16px; }
  .social .dot { width: 40px; height: 40px; border-radius: 50%; background: var(--ink); }
  .social .handle { font-weight: 600; }
  .footer {
    position: absolute; bottom: 0; left: 0; width: 100%; height: 165px;
    background: var(--ink); color: var(--white);
    display: flex; align-items: center; justify-content: center;
    font-size: 54px; font-weight: 600;
  }
</style>
</head>
<body>
  <main class="banner">
    <div class="brand-name">QUELLA STAFFING</div>

    <h1 class="headline">
      <span class="accent">HEALTHCARE</span>
      <span class="accent">RECRUITMENT</span>
      <span class="plain">AGENCY</span>
    </h1>

    <p class="tagline">Empowering your next<br>career move</p>

    <div class="illustration" role="img" aria-label="Cartoon group of five healthcare professionals in scrubs and lab coats standing in a clinic"></div>

    <p class="intro">Discover tailored opportunities<br>based on your career preference</p>

    <ul class="specialties">
      <li class="specialty">
        <svg viewBox="0 0 100 110" aria-hidden="true">
          <path d="M50 5 L90 20 V55 C90 80 72 98 50 106 C28 98 10 80 10 55 V20 Z" fill="#2a2fd0" stroke="#0b0b0b" stroke-width="5"/>
          <circle cx="50" cy="55" r="26" fill="#fff"/>
          <rect x="44" y="40" width="12" height="30" fill="#2a2fd0"/>
          <rect x="35" y="49" width="30" height="12" fill="#2a2fd0"/>
        </svg>
        <span>Allied health</span>
      </li>
      <li class="specialty">
        <svg viewBox="0 0 100 110" aria-hidden="true">
          <path d="M32 18 Q50 4 68 18 L66 30 H34 Z" fill="#0b0b0b"/>
          <rect x="46" y="12" width="8" height="14" fill="#fff"/>
          <rect x="43" y="16" width="14" height="6" fill="#fff"/>
          <circle cx="50" cy="48" r="18" fill="#2a2fd0"/>
          <path d="M16 106 C16 78 30 70 50 70 C70 70 84 78 84 106 Z" fill="#2a2fd0"/>
          <rect x="45" y="80" width="10" height="20" fill="#fff"/>
          <rect x="40" y="85" width="20" height="10" fill="#fff"/>
        </svg>
        <span>Nursing</span>
      </li>
      <li class="specialty">
        <svg viewBox="0 0 100 110" aria-hidden="true">
          <circle cx="26" cy="34" r="11" fill="#0b0b0b"/>
          <circle cx="50" cy="28" r="12" fill="#2a2fd0"/>
          <circle cx="74" cy="34" r="11" fill="#0b0b0b"/>
          <path d="M8 72 C8 56 16 50 26 50 C36 50 44 56 44 72 Z" fill="#0b0b0b"/>
          <path d="M56 72 C56 56 64 50 74 50 C84 50 92 56 92 72 Z" fill="#0b0b0b"/>
          <path d="M30 68 C30 50 40 44 50 44 C60 44 70 50 70 68 Z" fill="#2a2fd0"/>
          <rect x="43" y="60" width="14" height="44" fill="#2a2fd0"/>
          <rect x="30" y="73" width="40" height="14" fill="#2a2fd0"/>
        </svg>
        <span>Medical</span>
      </li>
    </ul>

    <h2 class="contact-title">GET IN TOUCH</h2>

    <div class="phone-pill">
      <svg viewBox="0 0 84 84" aria-hidden="true">
        <circle cx="42" cy="42" r="40" fill="#fff"/>
        <path d="M28 20 l8 12 -5 6 c3 7 8 12 15 15 l6 -5 12 8 -4 8 c-20 2 -42 -20 -40 -40 Z" fill="#2a2fd0"/>
        <path d="M48 22 a14 14 0 0 1 14 14 M48 30 a6 6 0 0 1 6 6" fill="none" stroke="#2a2fd0" stroke-width="4" stroke-linecap="round"/>
      </svg>
      <span>9000 123 456</span>
    </div>

    <div class="social">
      <span class="label">Follow us on</span>
      <span class="dot"></span>
      <span class="handle">@quellastaffing</span>
    </div>

    <footer class="footer">www.quellastaffing.com.au</footer>
  </main>
</body>
</html>
```